Velmora Consulting Business

** Please add the content information from my old business card
1. I would like to see a two sided business card with both options with the 1st Option--Tallow Spire-new WHITE BACKGROUND LOGO
2 nd Option-Tallow Spire - new BLACK- Background Logo
3rd -Option a business card with my Photo on the card
Please add the new word to the card information:
EXECUTION
AS THE OWNER'S REP
WE AIM TO ACHIEVE YOUR
INFRASTRUCTURE VISION with
OUR SPECIALIZATION & EXECUTION in:

FUNDING Planning
BUSINESS Planning
INFRASTRUCTURE Planning
PROJECT Management
Since 2012
_____________________________________________________________________
I want to get spot uv raised printing. I was liking a a nice rich white linen paper stock with black writing & NOT A COLORED CARD other than a variety of white or black cards concept

```html
<!DOCTYPE html>
<html lang="en">
<head>
<meta charset="utf-8">
<title>Velmora Consulting – Business Cards</title>
<link href="https://fonts.googleapis.com/css2?family=Source+Sans+3:wght@400;600;700&display=swap" rel="stylesheet">
<style>
  :root {
    --backdrop: #9b9b9b;
    --card-white: #f3f3f2;
    --card-black: #1f1e1e;
    --ink: #1c1c1c;
    --paper: #ffffff;
    --accent: #e3173e;
    --rule-light: #cfcfcf;
    --rule-dark: #3c3c3c;
  }
  * { margin: 0; padding: 0; box-sizing: border-box; }
  html, body {
    width: 1093px; height: 1200px; overflow: hidden;
    background: var(--backdrop);
    font-family: "Source Sans 3", "Myriad Pro", Arial, sans-serif;
  }
  .canvas { position: relative; width: 1093px; height: 1200px; }

  .card {
    position: absolute; left: 265px;
    width: 580px; height: 356px;
    border-radius: 26px;
    overflow: hidden;
  }
  .card--front { top: 226px; background: var(--card-white); color: var(--ink); }
  .card--back  { top: 621px; background: var(--card-black); color: var(--paper); }

  .divider { position: absolute; top: 74px; width: 1px; height: 208px; }
  .card--front .divider { left: 288px; background: var(--rule-light); }
  .card--back .divider  { left: 258px; background: var(--rule-dark); }

  .wordmark {
    position: absolute; width: 230px; text-align: center;
    font-weight: 600; line-height: 1;
  }
  .card--front .wordmark { left: 37px; top: 176px; color: var(--ink); }
  .card--back .wordmark  { left: 25px; top: 170px; color: var(--paper); }
  .wordmark__name { display: block; font-size: 50px; letter-spacing: -1px; }
  .wordmark__sub  { display: block; font-size: 14px; letter-spacing: 12.6px; margin-top: 8px; padding-left: 12px; }

  .person { position: absolute; left: 311px; top: 93px; }
  .person__name { font-size: 20.5px; font-weight: 700; white-space: nowrap; }
  .person__role { font-size: 14px; color: var(--accent); margin-top: 1px; padding-left: 2px; }

  .contacts { position: absolute; left: 311px; top: 160px; list-style: none; }
  .contacts li { display: flex; align-items: center; height: 21px; font-size: 16.5px; }
  .contacts svg { width: 15px; height: 15px; margin-right: 9px; flex: none; }

  .locations { position: absolute; left: 312px; top: 236px; font-size: 16.5px; white-space: nowrap; }
  .locations .dot { color: var(--accent); }

  .statement { position: absolute; left: 281px; top: 72px; font-size: 14.2px; line-height: 18.4px; text-transform: none; }
  .services { position: absolute; left: 281px; top: 185px; list-style: none; font-size: 14.2px; }
  .services li { display: flex; align-items: center; height: 18.4px; }
  .services .bullet { width: 7px; height: 7px; background: var(--accent); margin: 0 11px 0 2px; flex: none; }
  .since { position: absolute; left: 299px; top: 263px; font-size: 14.2px; }
</style>
</head>
<body>
<main class="canvas">

  <section class="card card--front" aria-label="Business card front">
    <div class="wordmark">
      <span class="wordmark__name">Velmora</span>
      <span class="wordmark__sub">CONSULTING</span>
    </div>
    <div class="divider"></div>

    <div class="person">
      <p class="person__name">Renata Halvorsen-Quill</p>
      <p class="person__role">CEO / LEAD PROJECT MANAGER</p>
    </div>

    <ul class="contacts">
      <li>
        <svg viewBox="0 0 16 16" aria-hidden="true"><path d="M3.5 1.5l2.5 3-1.5 1.6c.8 2 2.4 3.6 4.4 4.4L10.5 9l3 2.5-1.6 2.5C7 14 2 9 2 3.5z" fill="none" stroke="#1c1c1c" stroke-width="1.5" stroke-linejoin="round"/></svg>
        867.555.0198
      </li>
      <li>
        <svg viewBox="0 0 16 16" aria-hidden="true"><rect x="1" y="3.5" width="14" height="9" fill="#1c1c1c"/><path d="M1 3.5l7 5 7-5" fill="none" stroke="#f3f3f2" stroke-width="1.2"/></svg>
        renata@velmora.ca
      </li>
      <li>
        <svg viewBox="0 0 16 16" aria-hidden="true"><g fill="none" stroke="#1c1c1c" stroke-width="1.3"><circle cx="8" cy="8" r="6.5"/><ellipse cx="8" cy="8" rx="2.8" ry="6.5"/><path d="M1.5 8h13M2.5 4.8h11M2.5 11.2h11"/></g></svg>
        www.velmora.ca
      </li>
    </ul>

    <p class="locations">Northgate NT <span class="dot">•</span> Harrowby NB</p>
  </section>

  <section class="card card--back" aria-label="Business card back">
    <div class="wordmark">
      <span class="wordmark__name">Velmora</span>
      <span class="wordmark__sub">CONSULTING</span>
    </div>
    <div class="divider"></div>

    <p class="statement">
      EXECUTION<br>
      AS THE OWNER'S REP<br>
      WE AIM TO ACHIEVE YOUR<br>
      INFRASTRUCTURE VISION with<br>
      OUR SPECIALIZATION &amp; EXECUTION in:
    </p>

    <ul class="services">
      <li><span class="bullet"></span>FUNDING Planning</li>
      <li><span class="bullet"></span>BUSINESS Planning</li>
      <li><span class="bullet"></span>INFRASTRUCTURE Planning</li>
      <li><span class="bullet"></span>PROJECT Management</li>
    </ul>
    <p class="since">Since 2012</p>
  </section>

</main>
</body>
</html>
```